Sustainably Transforming Education

Company is education services based. early learning through adult and corporate. Focus is national government policy and program design and delivery alongside a research based and academically grounded set of approaches to planning, evaluation, and change management.I am looking for an innovative design position that aligns with the global agendas for innovation, creativity and collaboration at international and national policy levels (berulo is a name that reflects these qualities - colours need to reflect amythyst in some way). I also need a design that translates from a business card as 1 medium of interaction to a template that can work in word/powerpoint etc to support both stationery as well as a digital strategy across multiple channels (fb/twit/etc)There is no slogan/tag line for the company and their is no logo. I was looking to just leverage the name - have currently played around with various fonts (ending up with cuisine - all lowercase).

Industry/Entity Type

Adult

Contact Information for Business Card

name: berulo (all lowercase)Chairman: Andrew CrowMobile: +61 418 902 131Web: www.berulo.comemail: martin.pelly@berulo-example.com

Font styles to use
Script
Other font styles liked:
• cuisine

Colors
e34298
e667a6
33a6d7
aaaaaa

Requirements
Nice to have
• https://files.example-share.net/sh/qx7kw2hd91lzmnp/AAFr3tYbQeLp8VwZnKcDs2Hu?dl=0
• Link to the printwell templates used to begin this process....the one with the lines was about people intersecting (collaborating).....the organic shapes one more of a fluid feel of people coming together - the overall shape being largely spherical could represent a "global" feel.....anyway that is how I was thinking about these

```html
<!DOCTYPE html>
<html lang="en">
<head>
<meta charset="utf-8">
<title>berulo – Martin Pelly business card</title>
<link rel="stylesheet" href="https://fonts.googleapis.com/css2?family=Kaushan+Script&display=swap">
<style>
  :root {
    --amethyst: #e34298;
    --amethyst-light: #e667a6;
    --sky-blue: #33a6d7;
    --card-grey: #aaaaaa;
    --map-grey: #c4c4c4;
    --text-white: #ffffff;
    --text-dark: #1e1e1e;
    --script: "Kaushan Script", cursive;
  }
  * { margin: 0; padding: 0; box-sizing: border-box; }
  html, body {
    width: 1200px;
    height: 740px;
    overflow: hidden;
  }
  body {
    background: linear-gradient(225deg, var(--sky-blue) 0%, var(--amethyst-light) 55%, var(--amethyst) 100%);
  }
  .card {
    position: relative;
    width: 1200px;
    height: 740px;
    overflow: hidden;
    font-family: var(--script);
  }
  .card-shape {
    position: absolute;
    inset: 0;
    width: 1200px;
    height: 740px;
  }
  .card-shape .panel { fill: var(--card-grey); }
  .world-area {
    position: absolute;
    left: 0;
    top: 150px;
    width: 480px;
    height: 480px;
    border-radius: 0 48% 46% 0 / 0 40% 60% 0;
    background: radial-gradient(ellipse at 40% 45%, var(--map-grey) 0%, rgba(196,196,196,0.55) 55%, rgba(170,170,170,0) 80%);
  }
  .brand-name {
    position: absolute;
    left: 24px;
    top: 330px;
    font-size: 98px;
    letter-spacing: 4px;
    line-height: 1;
    color: var(--text-white);
  }
  .person {
    position: absolute;
    right: 78px;
    top: 70px;
    text-align: right;
  }
  .person-name {
    font-size: 104px;
    letter-spacing: 8px;
    line-height: 1.1;
    font-weight: 400;
    color: var(--text-white);
  }
  .person-title {
    margin-top: 0;
    font-size: 48px;
    letter-spacing: 2px;
    line-height: 1.1;
    color: var(--text-dark);
  }
  .contacts {
    position: absolute;
    left: 682px;
    top: 490px;
    list-style: none;
  }
  .contact-item {
    display: flex;
    align-items: center;
    height: 46px;
    color: var(--text-white);
    font-size: 27px;
    letter-spacing: 1px;
  }
  .contact-icon {
    width: 30px;
    height: 30px;
    margin-right: 32px;
    fill: var(--text-dark);
  }
</style>
</head>
<body>
  <main class="card">
    <svg class="card-shape" viewBox="0 0 1200 740" aria-hidden="true">
      <path class="panel" d="M0 0 H1045 Q1150 20 1165 45 Q1185 80 1200 118 V740 H132 Q60 730 40 690 Q20 640 0 566 Z"/>
    </svg>

    <div class="world-area" role="img" aria-label="Faint world map decoration"></div>

    <div class="brand-name">berulo</div>

    <header class="person">
      <h1 class="person-name">Martin Pelly</h1>
      <p class="person-title">Chairman</p>
    </header>

    <ul class="contacts">
      <li class="contact-item">
        <svg class="contact-icon" viewBox="0 0 24 24" aria-hidden="true">
          <path d="M3 9c0-3 4-5 9-5s9 2 9 5v1.5h-4.5V8.5c-1.5-.6-3-.8-4.5-.8s-3 .2-4.5.8v2H3z"/>
          <path d="M6 12l2-3h8l2 3v7H6z"/>
          <circle cx="12" cy="15" r="2" fill="#aaaaaa"/>
        </svg>
        <span>+61 427 315 086</span>
      </li>
      <li class="contact-item">
        <svg class="contact-icon" viewBox="0 0 24 24" aria-hidden="true">
          <path d="M2 5h20v14H2z"/>
          <path d="M3 6l9 7 9-7M3 18l7-6M21 18l-7-6" fill="none" stroke="#aaaaaa" stroke-width="1.3"/>
        </svg>
        <span>martin.pelly@berulo-example.com</span>
      </li>
      <li class="contact-item">
        <svg class="contact-icon" viewBox="0 0 24 24" aria-hidden="true">
          <circle cx="12" cy="12" r="10"/>
          <g fill="none" stroke="#aaaaaa" stroke-width="1.3">
            <ellipse cx="12" cy="12" rx="4" ry="10"/>
            <path d="M2 12h20M4 7h16M4 17h16M12 2v20"/>
          </g>
        </svg>
        <span>www.berulo-example.com</span>
      </li>
    </ul>
  </main>
</body>
</html>
```